Silver Meadow LLC business card

I help with the Marketing and Sales of various Natural, Organic, Eco Friendly and Healthy Main Stream products to Retail Corporate accounts as well as Independents and Distributors.I also highlight Private label items to these same Retail Corporate accounts.Cherish the Moments, Enjoy Life!

Speciality & Health Sales and Marketing

Target Market(s)

Men and Women

Industry/Entity Type

Business

Contact Information for Business Card

Silver Meadow, LLC
Janet Louise Verhagen
438 West Finch Lane
Ste 4-237
Phoenix, AZ 85047
602-555-0147
jverhagen@plumvale.net

Requirements
Must have
• Nice, femine font
Something in the background or on a side with a softness
Nice to have
• Cherish the Moments, Enjoy Life
Should not have
• Hardness

```html
<!DOCTYPE html>
<html lang="en">
<head>
<meta charset="utf-8">
<title>Silver Meadow LLC – Business Card</title>
<link rel="stylesheet" href="https://fonts.googleapis.com/css2?family=Nunito:wght@400;600;700;800&display=swap">
<style>
  :root {
    --backdrop: #161616;
    --card-white: #ffffff;
    --card-blush: #fdf1ea;
    --brand-orange: #f26a23;
    --brand-orange-soft: #f58a4f;
    --ink: #3a3a3a;
    --soft-grey: #ececec;
  }
  * { margin: 0; padding: 0; box-sizing: border-box; }
  html, body {
    width: 1200px; height: 900px; overflow: hidden;
    background: var(--backdrop);
    font-family: "Nunito", "Varela Round", Arial, sans-serif;
  }
  .stage { position: relative; width: 1200px; height: 900px; }
  .card { position: absolute; border-radius: 12px; overflow: hidden; }
  .card-front {
    left: 145px; top: 310px; width: 440px; height: 254px;
    background:
      radial-gradient(circle at 0% 100%, var(--card-blush) 0%, rgba(253,241,234,0) 55%),
      var(--card-white);
  }
  .card-back {
    left: 632px; top: 311px; width: 433px; height: 251px;
    background: radial-gradient(circle at 50% 35%, var(--brand-orange-soft) 0%, var(--brand-orange) 70%);
    display: flex; flex-direction: column; align-items: center;
  }
  .brand-dot {
    position: absolute; left: 40px; top: 66px;
    width: 100px; height: 100px; border-radius: 50%;
    background: var(--brand-orange);
  }
  .brand-name-front {
    position: absolute; left: 20px; top: 176px; width: 140px;
    text-align: center;
    font-weight: 700; font-size: 16px; color: var(--brand-orange);
    line-height: 1;
  }
  .details { position: absolute; left: 213px; top: 47px; color: var(--ink); }
  .person-name {
    font-size: 19px; font-weight: 700; color: var(--brand-orange);
    line-height: 24px; white-space: nowrap;
  }
  .person-role { font-size: 13.5px; line-height: 17px; }
  .address { margin-top: 10px; font-size: 13px; line-height: 15px; }
  .contacts { list-style: none; margin-top: 13px; font-size: 13px; line-height: 16.5px; }
  .contacts li { display: flex; align-items: center; gap: 8px; white-space: nowrap; }
  .contacts svg { width: 10px; height: 10px; flex: none; fill: var(--brand-orange); }
  .back-dot {
    margin-top: 58px;
    width: 94px; height: 94px; border-radius: 50%;
    background: var(--soft-grey);
  }
  .brand-name-back {
    margin-top: 18px;
    font-weight: 800; font-size: 30px; letter-spacing: 0.5px;
    color: var(--soft-grey); line-height: 1;
  }
</style>
</head>
<body>
<main class="stage">
  <section class="card card-front" aria-label="Card front">
    <div class="brand-dot"></div>
    <div class="brand-name-front">Silver Meadow</div>
    <div class="details">
      <h1 class="person-name">Janet Louise Verhagen</h1>
      <p class="person-role">Managing Director</p>
      <p class="address">438 West Finch Lane, Ste 4-237<br>Phoenix, AZ 85047</p>
      <ul class="contacts">
        <li><svg viewBox="0 0 10 10"><path d="M2.5 0h5a1 1 0 0 1 1 1v8a1 1 0 0 1-1 1h-5a1 1 0 0 1-1-1V1a1 1 0 0 1 1-1zm.5 1.2v6.3h4V1.2z"/></svg>602-555-0147</li>
        <li><svg viewBox="0 0 10 10"><path d="M0 3.5C1 1 9 1 10 3.5L8.5 4.8 7 3.8V3H3v.8L1.5 4.8zM2 5.5h6L9 9H1z"/></svg>602-555-0147</li>
        <li><svg viewBox="0 0 10 10"><path d="M2.5 0h5v3h2v6h-9V3h2zm1 1v2h3V1zM2 5v1h6V5z"/></svg>602-555-0147</li>
        <li><svg viewBox="0 0 10 10"><path d="M0 2h10v.8L5 5.8 0 2.8zm0 1.9 5 3 5-3V8H0z"/></svg>jverhagen@plumvale.net</li>
        <li><svg viewBox="0 0 10 10"><path d="M4 6 6 4l.7.7-2 2zM5.5 1.5a2 2 0 0 1 3 3L7.3 5.7l-.7-.7 1.2-1.2a1 1 0 0 0-1.6-1.6L5 3.4l-.7-.7zM1.5 5.5 2.7 4.3l.7.7-1.2 1.2a1 1 0 0 0 1.6 1.6L5 6.6l.7.7-1.2 1.2a2 2 0 0 1-3-3z"/></svg>www.silvermeadow.net</li>
      </ul>
    </div>
  </section>

  <section class="card card-back" aria-label="Card back">
    <div class="back-dot"></div>
    <p class="brand-name-back">SILVER MEADOW LLC</p>
  </section>
</main>
</body>
</html>
```